Catering Company Website Design

We are working with a bbq catering company in California called Ember Plank Catering.
Some sites to use for content/competitors and inspiration:
https://19parsnips.com
https://mbetrovandel.com
https://ridgefeastco.com
https://tinforkdenvale.com (client's favorite)
https://www.marvenasmokehut.com (client's favorite)
https://www.theopenkettlekitchen.com
Thank you for taking the time to consider designing a website for us. We are web developers based in Stockton, CA, USA. Most of our projects go through the same process. Understanding this process may help you win a project with us. We custom-code all of our websites in-house. We don’t have any requirements as to what tools you use for your design, but we prefer Figma files. For any design that we label as four-stars, we send it to the client for review. The client picks the final design they want us to use. Once we complete this process, we will continue to show additional clients all the four-star sites and purchase them later. Your designs will have multiple chances to sell. For better chances of success, we ask that you follow these guidelines.
IMAGES:
If you use any images or icons in the design, we ask that you have a link to the asset so we can purchase the image/icon. Most of the designs we submit do not have the customer’s images on them unless they have some great images. Be creative; show us the feeling you are trying to portray with your image choices. Use any royalty-free site you choose. We subscribe to Zelvio and mainly use their images, but we can purchase images outside of Zelvio.
PLEASE NOTE: we will not submit designs to clients with watermarks on the images.
FONTS:
We ask that you identify the fonts used in the design. This can be done in a message if you want. We typically use Google Fonts and Zelvio Fonts.
CONTENT:
We're always open to different content and ideas. We often submit designs with stock images so the client can see our vision. We typically take pictures after the website launch to use their images with our vision. Lorem Ipsum is fine for paragraphs, but we ask that you write the headers in correct English. We want to be able to show the vision and identify the sections of the website.
INSPIRATION:
We typically add a couple of links in the brief of websites we like to help you get started in your design.
REVISIONS:
We do not often ask for revisions of the designs unless we see something in the design that may not appeal to the client. If there are slight changes that we want to make, we do that in the development process.
FEEDBACK:
We rarely give feedback on designs during the design process. We are working on many website projects and do not have the time to provide feedback. We usually respond if your request is well thought out and asks specific questions, but a note asking “feedback, please” usually goes unanswered

```html
<!DOCTYPE html>
<html lang="en">
<head>
<meta charset="utf-8">
<title>Ember Plank Catering</title>
<link href="https://fonts.googleapis.com/css2?family=Merriweather+Sans:wght@400;700;800&family=Poppins:wght@400;500;600&display=swap" rel="stylesheet">
<style>
:root{
  --red:#c8161d;
  --maroon:#3b0d07;
  --footer:#3a1209;
  --ink:#1f1a18;
  --body:#444;
  --white:#fff;
}
*{box-sizing:border-box;margin:0;padding:0}
html,body{width:1200px;height:5128px;overflow:hidden}
body{position:relative;background:var(--white);font-family:"Poppins",sans-serif;color:var(--body)}
.abs{position:absolute}
a{text-decoration:none;color:inherit}

/* header */
.brand{display:flex;align-items:center;gap:8px;font-family:"Merriweather Sans",sans-serif;font-weight:800;color:var(--maroon);font-size:13px;line-height:1.1;width:130px}
.brand .dot{width:18px;height:18px;border-radius:50%;background:var(--red);flex:none}
.nav{left:296px;top:39px;display:flex;gap:31px;font-size:14px;font-weight:500;color:var(--ink);text-transform:uppercase}
.nav .active{color:var(--red);border-bottom:2px solid var(--red);padding-bottom:2px}
.cart{left:904px;top:34px}
.btn{display:inline-flex;align-items:center;justify-content:center;font-weight:600;color:#fff;background:var(--red)}
.contact{left:956px;top:26px;width:132px;height:46px;font-size:14px}

/* hero */
.hero{left:0;top:98px;width:1200px;height:602px;
  background:
    radial-gradient(ellipse 190px 150px at 720px 520px,rgba(255,170,40,.95),rgba(240,90,20,.75) 45%,rgba(120,30,10,0) 100%),
    radial-gradient(ellipse 140px 170px at 690px 250px,rgba(150,45,40,.95),rgba(95,30,28,.7) 55%,rgba(40,20,18,0) 100%),
    radial-gradient(ellipse 260px 220px at 760px 470px,rgba(200,60,15,.55),rgba(60,20,10,0) 100%),
    radial-gradient(ellipse 300px 260px at 180px 200px,rgba(70,20,18,.45),rgba(0,0,0,0) 100%),
    linear-gradient(90deg,#151414 0%,#1d1b1a 50%,#141312 100%)}
.hero h1{left:110px;top:124px;font-family:"Merriweather Sans",sans-serif;font-weight:800;font-size:48px;line-height:58px;color:#fff;text-transform:uppercase;letter-spacing:.5px}
.hero p{left:112px;top:252px;width:400px;font-size:13.5px;line-height:30px;color:#eee}
.hero .btn{left:112px;top:364px;width:134px;height:48px;font-size:13px;text-transform:uppercase}

/* section heads */
.center-title{left:0;width:1200px;text-align:center;font-family:"Merriweather Sans",sans-serif;font-weight:700;color:var(--ink)}
.center-title span{color:var(--red)}
.eyebrow{font-size:19px;color:var(--red);font-family:"Merriweather Sans",sans-serif;font-weight:400}
.lead{left:130px;width:940px;text-align:center;font-size:14px;line-height:31px}

/* feature cards */
.card{background:#fff;box-shadow:0 4px 18px rgba(0,0,0,.12);padding:44px 22px 0 22px}
.card h3{font-family:"Merriweather Sans",sans-serif;font-weight:700;font-size:29px;color:var(--maroon);margin:6px 0 10px;white-space:nowrap}
.card h3 span{color:var(--red)}
.card p{font-size:14px;line-height:31px}
.more{display:inline-flex;align-items:center;gap:10px;margin-top:16px;font-family:"Merriweather Sans",sans-serif;font-weight:700;font-size:14px;color:var(--ink)}
.more svg{width:28px;height:12px}

/* offerings */
.offer{top:1706px;width:310px;height:450px;background:#fff;box-shadow:0 4px 18px rgba(0,0,0,.1);text-align:center}
.offer .ph{height:222px}
.offer h4{font-family:"Merriweather Sans",sans-serif;font-weight:700;font-size:20px;color:var(--ink);margin:28px 0 10px}
.offer p{font-size:13.5px;line-height:28px;padding:0 28px}
.offer .btn{position:absolute;left:22px;right:22px;bottom:24px;height:42px;font-size:15px;background:var(--maroon);font-family:"Merriweather Sans",sans-serif;font-weight:700}
.offer .btn.hot{background:var(--red)}

/* cta */
.cta-card{left:274px;top:4372px;width:652px;height:238px;background:#fff;text-align:center;padding-top:38px}
.cta-card h2{font-family:"Merriweather Sans",sans-serif;font-weight:700;font-size:30px;color:var(--maroon)}
.cta-card p{font-size:14px;line-height:31px;margin:14px 90px 0}
.cta-card .btn{margin-top:14px;width:256px;height:42px;font-size:14px;font-family:"Merriweather Sans",sans-serif;font-weight:700}

/* footer */
.footer{left:0;top:4680px;width:1200px;height:448px;background:var(--footer);color:#fff}
.footer .brand{color:#fff}
.fnav{left:264px;top:136px;display:flex;gap:30px;font-size:14px;font-weight:500;text-transform:uppercase}
.social{top:124px;width:34px;height:34px;border:2px solid #fff;border-radius:50%}
.news{left:112px;top:212px;font-size:14px;text-transform:uppercase;padding-bottom:14px;border-bottom:1px solid #8a6a62;width:472px}
.email{left:112px;top:270px;width:338px;height:42px;background:#fff;color:#333;font-size:14px;padding:12px;text-transform:uppercase}
.submit{left:472px;top:278px;font-family:"Merriweather Sans",sans-serif;font-weight:800;font-size:19px}
.badge{top:206px;width:114px;height:98px;background:#fff;border-radius:6px;box-shadow:inset 0 0 0 6px #f1ebe8}
.copy{left:112px;top:374px;font-size:14px}
</style>
</head>
<body>

<header>
  <div class="abs brand" style="left:112px;top:30px"><span class="dot"></span>Ember Plank Catering</div>
  <nav class="abs nav">
    <a class="active">Home</a><a>Menu</a><a>Reservations</a><a>Order Online</a><a>Catering</a><a>Shop</a>
  </nav>
  <svg class="abs cart" width="32" height="30" viewBox="0 0 32 30" aria-label="Cart">
    <path d="M2 5h5l4 14h13l3-10H9" fill="none" stroke="#222" stroke-width="2"/>
    <circle cx="13" cy="24" r="2" fill="#222"/><circle cx="22" cy="24" r="2" fill="#222"/>
    <circle cx="26" cy="6" r="6" fill="#111"/><text x="26" y="9" font-size="8" fill="#fff" text-anchor="middle" font-family="Poppins,sans-serif">0</text>
  </svg>
  <a class="abs btn contact">CONTACT US</a>
</header>

<section class="abs hero" role="img" aria-label="Grilled meat skewered on a fork over flames">
  <h1 class="abs">Ember Plank<br>Catering</h1>
  <p class="abs">Lorem ipsum dolor sit amet, consectetur adipiscing elit, sed do eiusmod tempor incididunt ut labore et dolore magna aliqua.</p>
  <a class="abs btn">Get Started</a>
</section>

<h2 class="abs center-title" style="top:776px;font-size:31px">ABOUT EMBER PLANK <span>CATERING</span></h2>
<p class="abs lead" style="top:832px">Lorem ipsum dolor sit amet, consectetur adipiscing elit, sed do eiusmod tempor incididunt ut labore et dolore magna aliqua. Ut enim ad minim veniam, quis nostrud exercitation ullamco laboris nisi ut aliquip ex ea commodo consequat. Duis aute irure dolor in reprehenderit in voluptate velit esse cillum dolore eu fugiat nulla pariatur.</p>

<div class="abs" style="left:0;top:970px;width:360px;height:330px;background:linear-gradient(90deg,#f9eded,#fdf6f6)" role="img" aria-label="Faint repeating flame pattern"></div>
<div class="abs" style="left:360px;top:970px;width:728px;height:406px;background:
  radial-gradient(circle 70px at 470px 60px,rgba(255,245,200,1),rgba(250,210,120,.6) 50%,rgba(250,200,110,0) 100%),
  radial-gradient(ellipse 260px 110px at 520px 330px,rgba(235,205,140,.85),rgba(200,160,100,0) 100%),
  radial-gradient(ellipse 300px 120px at 260px 320px,rgba(140,85,60,.85),rgba(120,70,50,0) 100%),
  linear-gradient(180deg,#4a5048 0%,#6c6650 38%,#8a6f52 62%,#5c3d2c 100%)" role="img" aria-label="Guests at an outdoor charcuterie table at sunset"></div>
<div class="abs card" style="left:112px;top:1246px;width:488px;height:264px">
  <div class="eyebrow">Our Story</div>
  <h3>Trusted for <span>Over 20 Years</span></h3>
  <p>Lorem ipsum dolor sit amet, consectetur adipiscing elit, sed do eiusmod tempor incididunt ut labore et dolore magna aliqua.</p>
  <a class="more">Learn About Ember Plank Catering <svg viewBox="0 0 28 12"><path d="M0 6h26M21 1l5 5-5 5" fill="none" stroke="#222" stroke-width="1.6"/></svg></a>
</div>

<div class="abs center-title eyebrow" style="top:1596px;font-weight:400">Our Offerings</div>
<h2 class="abs center-title" style="top:1634px;font-size:33px">We’ve Got You Covered</h2>

<div class="abs offer" style="left:112px">
  <div class="ph" style="background:
    radial-gradient(ellipse 90px 50px at 70px 80px,rgba(240,180,80,.9),rgba(200,120,40,0) 100%),
    radial-gradient(ellipse 90px 50px at 230px 100px,rgba(235,170,70,.9),rgba(200,120,40,0) 100%),
    radial-gradient(ellipse 170px 60px at 155px 170px,rgba(120,60,25,.9),rgba(90,40,20,0) 100%),
    linear-gradient(180deg,#2b2420 0%,#6a4526 55%,#3a2414 100%)" role="img" aria-label="Rows of mini burgers on a board"></div>
  <h4>Catered Events</h4>
  <p>Lorem ipsum dolor sit amet, eiusmod tempor incididunt ut labore et dolore magna aliqua.</p>
  <a class="btn">Learn About Our Events</a>
</div>
<div class="abs offer" style="left:446px">
  <div class="ph" style="background:
    radial-gradient(ellipse 160px 50px at 170px 160px,rgba(215,110,50,.85),rgba(180,80,30,0) 100%),
    radial-gradient(ellipse 120px 80px at 220px 60px,rgba(200,215,220,.8),rgba(160,180,190,0) 100%),
    linear-gradient(180deg,#3c464a 0%,#5e6a6c 45%,#3a3532 100%)" role="img" aria-label="Workplace buffet line with hot dishes"></div>
  <h4>Workplace Dining</h4>
  <p>Lorem ipsum dolor sit amet, eiusmod tempor incididunt ut labore et dolore magna aliqua.</p>
  <a class="btn hot">Learn About Workplace Dining</a>
</div>
<div class="abs offer" style="left:780px">
  <div class="ph" style="background:
    radial-gradient(circle 45px at 60px 60px,rgba(60,50,40,.85),rgba(60,50,40,0) 100%),
    radial-gradient(circle 45px at 250px 70px,rgba(70,55,40,.85),rgba(70,55,40,0) 100%),
    radial-gradient(circle 45px at 150px 150px,rgba(190,70,40,.7),rgba(190,70,40,0) 100%),
    radial-gradient(circle 45px at 260px 180px,rgba(60,45,35,.85),rgba(60,45,35,0) 100%),
    radial-gradient(circle 45px at 50px 185px,rgba(90,110,50,.7),rgba(90,110,50,0) 100%),
    #eeebe7" role="img" aria-label="Meal prep containers with grilled food"></div>
  <h4>Delivery</h4>
  <p>Lorem ipsum dolor sit amet, eiusmod tempor incididunt ut labore et dolore magna aliqua.</p>
  <a class="btn">Learn About Delivery</a>
</div>

<div class="abs" style="left:112px;top:2254px;width:976px;height:510px;background:
  radial-gradient(ellipse 380px 60px at 560px 130px,rgba(255,225,150,.7),rgba(255,210,130,0) 100%),
  radial-gradient(ellipse 260px 120px at 230px 430px,rgba(220,150,60,.85),rgba(200,120,50,0) 100%),
  radial-gradient(ellipse 300px 90px at 560px 420px,rgba(150,90,45,.85),rgba(140,80,40,0) 100%),
  radial-gradient(ellipse 260px 140px at 640px 90px,rgba(110,125,130,.8),rgba(100,110,110,0) 100%),
  linear-gradient(180deg,#55635c 0%,#7a7560 40%,#9b7a52 70%,#6a4a30 100%)" role="img" aria-label="Backyard party with string lights and a food table"></div>
<div class="abs card" style="left:574px;top:2614px;width:514px;height:248px">
  <div class="eyebrow">Our Food</div>
  <h3>Quality Food Made From Scratch</h3>
  <p>Lorem ipsum dolor sit amet, consectetur adipiscing elit, sed do eiusmod tempor incididunt ut labore et dolore magna aliqua.</p>
  <a class="more">Learn About Our Food <svg viewBox="0 0 28 12"><path d="M0 6h26M21 1l5 5-5 5" fill="none" stroke="#222" stroke-width="1.6"/></svg></a>
</div>

<div class="abs" style="left:112px;top:2948px;width:976px;height:508px;background:
  radial-gradient(ellipse 200px 230px at 900px 170px,rgba(25,25,25,.95),rgba(30,30,28,0) 100%),
  radial-gradient(ellipse 260px 80px at 700px 390px,rgba(200,120,60,.85),rgba(190,100,50,0) 100%),
  radial-gradient(ellipse 90px 40px at 420px 280px,rgba(210,40,30,.8),rgba(200,40,30,0) 100%),
  radial-gradient(ellipse 280px 200px at 200px 120px,rgba(200,150,80,.6),rgba(180,130,70,0) 100%),
  linear-gradient(180deg,#7a6a40 0%,#5e6a3a 45%,#3e4a26 100%)" role="img" aria-label="Guests mingling beside a kettle grill full of food"></div>
<div class="abs card" style="left:112px;top:3308px;width:514px;height:244px">
  <div class="eyebrow">BBQ Catering</div>
  <h3>California Catering Authority</h3>
  <p>Lorem ipsum dolor sit amet, consectetur adipiscing elit, sed do eiusmod tempor incididunt ut labore et dolore magna aliqua.</p>
  <a class="more">Learn About Our Food <svg viewBox="0 0 28 12"><path d="M0 6h26M21 1l5 5-5 5" fill="none" stroke="#222" stroke-width="1.6"/></svg></a>
</div>

<div class="abs" style="left:112px;top:3646px;width:976px;height:552px;background:
  radial-gradient(ellipse 160px 110px at 110px 330px,rgba(130,60,30,.95),rgba(110,50,25,0) 100%),
  radial-gradient(ellipse 170px 120px at 870px 330px,rgba(120,45,25,.95),rgba(100,40,20,0) 100%),
  radial-gradient(ellipse 420px 90px at 490px 500px,rgba(250,160,40,.9),rgba(230,110,20,0) 100%),
  linear-gradient(180deg,#5f7a3e 0%,#6e7a3a 35%,#5a3a20 70%,#2e1a0e 100%)" role="img" aria-label="Sausages and ribs sizzling on a flaming grill"></div>
<div class="abs" style="left:348px;top:3768px;width:490px;height:286px;background:#fff;text-align:center;padding:38px 26px 0">
  <h3 style="font-family:'Merriweather Sans',sans-serif;font-weight:700;font-size:23px;color:var(--maroon);margin-bottom:10px">BBQ Catering</h3>
  <p style="font-size:13.5px;line-height:31px">Lorem ipsum dolor sit amet, consectetur adipiscing elit, sed do eiusmod tempor incididunt ut labore et dolore magna aliqua. Ut enim ad minim veniam, quis nostrud exercitation ullamco laboris nisi ut aliquip ex ea commodo consequat.</p>
  <a class="more" style="color:var(--red);margin-top:10px">Learn About Our Food <svg viewBox="0 0 28 12"><path d="M0 6h26M21 1l5 5-5 5" fill="none" stroke="#c8161d" stroke-width="1.6"/></svg></a>
</div>

<div class="abs" style="left:0;top:4290px;width:600px;height:390px;background:
  radial-gradient(ellipse 140px 160px at 40px 120px,rgba(90,150,50,.95),rgba(80,130,40,0) 100%),
  radial-gradient(ellipse 220px 120px at 200px 250px,rgba(240,225,195,.95),rgba(230,210,180,0) 100%),
  linear-gradient(180deg,#2e3a2a 0%,#3a3632 60%,#4a4644 100%)" role="img" aria-label="Grilled wrap with fresh greens"></div>
<div class="abs" style="left:600px;top:4290px;width:600px;height:390px;background:
  radial-gradient(ellipse 80px 60px at 540px 60px,rgba(250,250,248,1),rgba(240,240,236,0) 100%),
  radial-gradient(ellipse 160px 120px at 430px 220px,rgba(190,120,60,.85),rgba(180,110,50,0) 100%),
  radial-gradient(ellipse 140px 80px at 140px 60px,rgba(230,170,60,.6),rgba(230,170,60,0) 100%),
  linear-gradient(135deg,#ece8e2 0%,#e2dad0 50%,#f3f1ee 100%)" role="img" aria-label="Chicken skewers with dipping sauce on a plate"></div>
<div class="abs cta-card">
  <h2>Ready to plan your unique experience?</h2>
  <p>Lorem ipsum dolor sit amet, consectetur adipiscing elit, sed do eiusmod tempor incididunt ut labore et dolore magna aliqua.</p>
  <a class="btn">Contact an Event Specialist</a>
</div>

<footer class="abs footer">
  <div class="abs brand" style="left:112px;top:124px"><span class="dot"></span>Ember Plank Catering</div>
  <nav class="abs fnav"><a>Home</a><a>Menu</a><a>Reservations</a><a>Order Online</a><a>Catering</a><a>Shop</a></nav>
  <span class="abs social" style="left:962px" aria-label="Social link"></span>
  <span class="abs social" style="left:1008px" aria-label="Social link"></span>
  <span class="abs social" style="left:1054px" aria-label="Social link"></span>
  <div class="abs news">Sign up for our newsletter</div>
  <div class="abs email">Email</div>
  <div class="abs submit">SUBMIT</div>
  <span class="abs badge" style="left:708px" aria-label="Partner badge"></span>
  <span class="abs badge" style="left:840px" aria-label="Partner badge"></span>
  <span class="abs badge" style="left:972px" aria-label="Partner badge"></span>
  <div class="abs copy">© 2024 Ember Plank Catering, LTD. | 1234 W. Harlan St. | Brookvale CA 95202</div>
</footer>

</body>
</html>
```